Website Design for Employee Moral and Happiness Company

Looking for a clean website design that explains our features in a step by step manner so our visitors know exactly what our site does before logging in.

The site is called "Velrato". See logo design and video for a sample of style and an overview of what we do.

Target Market(s)

Business owners that are looking to retain employees.

Number of Pages Required

1 page

```html
<!DOCTYPE html>
<html lang="en">
<head>
<meta charset="UTF-8">
<title>Velrato — Employee Morale & Happiness</title>
<link href="https://fonts.googleapis.com/css2?family=Old+Standard+TT:wght@400;700&family=Montserrat:wght@400;500;600;700&display=swap" rel="stylesheet">
<style>
:root{
  --orange:#f0520f;
  --ink:#1b1b1b;
  --text:#3d3d3d;
  --muted:#6b6b6b;
  --line:#d9d9d9;
  --panel:#e2d9cb;
  --blog-bg:#ececec;
  --white:#ffffff;
}
*{margin:0;padding:0;box-sizing:border-box}
html,body{width:1200px;height:3665px;overflow:hidden;background:var(--white)}
body{font-family:"Montserrat",sans-serif;color:var(--text)}
.page{position:relative;width:1200px;height:3665px;overflow:hidden}
.abs{position:absolute}
.serif{font-family:"Old Standard TT",serif;font-weight:700;color:var(--ink)}
.brand{font-family:"Old Standard TT",serif;font-weight:700;color:var(--ink);letter-spacing:1px}
.fill{position:absolute;border-radius:6px}

/* nav */
.nav-brand{left:111px;top:34px;font-size:56px;line-height:1}
.nav a{position:absolute;top:62px;font-size:13px;font-weight:600;color:var(--ink);text-decoration:none}
.nav a.active{color:var(--orange)}
.nav a.active::after{content:"";position:absolute;left:0;right:0;bottom:-10px;height:2px;background:var(--orange)}
.login{left:921px;top:47px;width:129px;height:41px;border-radius:21px;background:var(--orange);box-shadow:0 0 0 2px #fff,0 0 0 3px var(--orange);color:#fff;font-size:13px;font-weight:600}
.login span{position:absolute;left:21px;top:12px}
.login i{position:absolute;right:8px;top:8px;width:26px;height:26px;border-radius:50%;background:#fff}

/* hero */
.hero-title{left:111px;top:218px;font-size:82px;line-height:1}
.hero-sub{left:111px;top:310px;width:440px;font-size:18px;line-height:29px;font-weight:600;color:#2d2d2d}
.mail{height:43px;border:1.5px solid #9a9a9a;border-radius:22px;background:#fff}
.mail .ph{position:absolute;left:14px;top:13px;font-size:13px;color:#555}
.mail .btn{position:absolute;right:3px;top:3px;height:34px;border-radius:17px;background:var(--orange);color:#fff;font-size:13px;font-weight:600;text-align:center;line-height:34px}
.member{font-size:13px;color:#444}
.member b{color:var(--orange);font-weight:600;text-decoration:underline}

/* sections */
.kicker{font-size:15px;letter-spacing:6px;font-weight:500;color:var(--orange)}
.h2{font-size:41px;line-height:1}
.rule{height:3px;background:var(--orange)}
.center{left:0;width:1200px;text-align:center}
.para{font-size:14.5px;line-height:25.6px;color:#444}
.pill{border-radius:19px;background:var(--orange);color:#fff;font-size:13px;font-weight:600;text-align:center}

/* video */
.video{left:182px;top:1234px;width:836px;height:422px;border:3px solid var(--orange);border-radius:18px;background:var(--panel);box-shadow:0 22px 30px rgba(0,0,0,.18)}
.play{left:504px;top:1411px;width:68px;height:68px;border-radius:50%;background:var(--orange)}
.play-label{left:589px;top:1434px;font-size:17px;font-weight:500;color:#fff;letter-spacing:.5px}

/* feature cards */
.card{position:absolute;background:#fff;box-shadow:0 2px 8px rgba(0,0,0,.2)}
.feature{top:1898px;width:309px;height:333px;text-align:center}
.feature h3{position:absolute;top:140px;left:0;right:0;font-size:26px}
.feature p{position:absolute;top:186px;left:18px;right:18px;font-size:12.5px;line-height:20.5px;color:#666}
.feature .more{position:absolute;top:286px;left:0;right:0;font-family:"Old Standard TT",serif;font-size:13px;color:#333}
.more u{margin-right:8px}
.arrow{display:inline-block;width:19px;height:19px;border-radius:50%;background:var(--orange);vertical-align:middle;position:relative}
.arrow svg{position:absolute;left:4px;top:4px}
.dots-nav span{display:inline-block;width:9px;height:9px;border-radius:50%;border:1px solid #555;margin:0 2px}
.dots-nav span.on{background:var(--orange);border-color:var(--orange)}

/* blog */
.blog-band{left:0;top:2363px;width:1200px;height:702px;background:linear-gradient(160deg,#f1f1f1,#e4e4e4 60%,#ededed)}
.post{top:2555px;width:466px;height:363px}
.post .tag{position:absolute;left:14px;top:204px;font-size:14px;color:var(--orange)}
.post h3{position:absolute;left:14px;top:232px;width:430px;font-size:26px;line-height:35px;font-weight:400}
.post .meta{position:absolute;left:14px;top:312px;font-size:13px;color:#555}
.meta .ico{display:inline-block;vertical-align:middle;margin-right:6px}
.meta .gap{display:inline-block;width:44px}

/* footer */
.f-col h4{font-size:20px;font-weight:700}
.f-col .u{width:22px;height:2px;background:var(--orange);margin:12px 0 13px}
.f-col li{list-style:none;font-size:13px;color:#444;line-height:25.8px}
.legal{font-size:11px;font-weight:500;color:#333}
</style>
</head>
<body>
<div class="page">

  <!-- Navigation -->
  <header class="nav">
    <div class="abs brand nav-brand">velrato</div>
    <a class="active" style="left:451px">Home</a>
    <a style="left:528px">About Us</a>
    <a style="left:626px">Our Features</a>
    <a style="left:747px">FAQs</a>
    <a style="left:821px">Contact Us</a>
    <div class="abs login"><span>Log In</span><i><svg width="26" height="26" viewBox="0 0 26 26"><circle cx="13" cy="10" r="3.5" fill="#1b1b1b"/><path d="M7 19c0-3.5 2.7-5 6-5s6 1.5 6 5z" fill="#1b1b1b"/></svg></i></div>
  </header>

  <!-- Hero -->
  <section class="hero">
    <h1 class="abs brand hero-title">velrato</h1>
    <p class="abs hero-sub">Perspiciatisunde omnisiste errorsit voluptatem accusantium doloremque laudantium.</p>
    <div class="abs mail" style="left:111px;top:397px;width:373px"><span class="ph">Enter Mail</span><span class="btn" style="width:112px">Get Started</span></div>
    <p class="abs member" style="left:127px;top:452px">Already a member? <b>Sign In</b></p>
    <div class="fill" role="img" aria-label="Illustration of a team of four colleagues greeting and shaking hands in an office" style="left:576px;top:182px;width:506px;height:359px;background:linear-gradient(135deg,#f3f3f3,#e6e9ea 60%,#f6e1d6)"></div>
  </section>

  <div class="fill" role="img" aria-label="Decorative dot grid" style="left:1060px;top:566px;width:140px;height:231px;background:#f4f4f4;border-radius:50% 0 0 50%"></div>

  <!-- About -->
  <section class="about">
    <div class="fill" role="img" aria-label="Illustration of a presenter pointing at a rising growth chart on a projector screen" style="left:114px;top:648px;width:427px;height:477px;background:linear-gradient(160deg,#faf3e0,#f1ece4 55%,#e9e9e9)"></div>
    <p class="abs kicker" style="left:609px;top:742px">WHO WE ARE</p>
    <h2 class="abs serif h2" style="left:609px;top:773px">About Us</h2>
    <div class="abs rule" style="left:609px;top:824px;width:94px"></div>
    <p class="abs para" style="left:609px;top:844px;width:470px">Perspiciatis unde omnis iste natus error sit voluptatem accusantium doloremque laudantium, totam rem aperiam, eaque ipsa quaeab illo inventore veritatis et quasi architecto beatae vitae dicta sunt explicabo. Nemo enim ipsam voluptatem quia voluptas sit aspernatur aut odit aut fugit, sed quia consequuntur magni dolores eos qui ratione voluptatem sequi nesciunt.</p>
    <div class="abs pill" style="left:609px;top:1042px;width:145px;height:37px;line-height:37px">Learn More</div>
  </section>

  <!-- Video -->
  <section>
    <div class="abs video"></div>
    <div class="fill" role="img" aria-label="Illustrated instant photos of smiling team members pinned to the board" style="left:300px;top:1290px;width:600px;height:290px;background:linear-gradient(90deg,#f4ede1,#e9e2d6 50%,#f2ebdf)"></div>
    <div class="abs play"><svg width="68" height="68" viewBox="0 0 68 68"><path d="M28 24l16 10-16 10z" fill="#fff"/></svg></div>
    <div class="abs play-label">PLAY VIDEO</div>
  </section>

  <div class="fill" role="img" aria-label="Decorative dot grid" style="left:0;top:1658px;width:121px;height:235px;background:#f4f4f4;border-radius:0 50% 50% 0"></div>

  <!-- Features -->
  <section>
    <p class="abs kicker center" style="top:1778px">WHAT WE DO</p>
    <h2 class="abs serif h2 center" style="top:1809px">Our Features</h2>
    <div class="abs rule" style="left:553px;top:1858px;width:94px"></div>

    <article class="card feature" style="left:111px">
      <div class="fill" role="img" aria-label="Illustration of a person reaching for floating documents" style="left:95px;top:17px;width:120px;height:113px;background:#f3ede9"></div>
      <h3 class="serif" style="font-weight:400">Suibusdam Atautofici</h3>
      <p>Soiejpiciatis unde omnis iste natus error sit voluptatem accusantium doloremque laudantium, totam rem aperiam, eaque ipsa quae ab illo inventore veritatis et quasi</p>
      <div class="more"><u>Learn More</u><span class="arrow"><svg width="11" height="11" viewBox="0 0 11 11"><path d="M2 5.5h7M6 2.5l3 3-3 3" stroke="#fff" stroke-width="1.4" fill="none"/></svg></span></div>
    </article>
    <article class="card feature" style="left:446px">
      <div class="fill" role="img" aria-label="Illustration of a person uploading a file to a screen" style="left:95px;top:17px;width:120px;height:113px;background:#f3ede9"></div>
      <h3 class="serif" style="font-weight:400">Faerum Necessitati</h3>
      <p>Soiejpiciatis unde omnis iste natus error sit voluptatem accusantium doloremque laudantium, totam rem aperiam, eaque ipsa quae ab illo inventore veritatis et quasi</p>
      <div class="more"><u>Learn More</u><span class="arrow"><svg width="11" height="11" viewBox="0 0 11 11"><path d="M2 5.5h7M6 2.5l3 3-3 3" stroke="#fff" stroke-width="1.4" fill="none"/></svg></span></div>
    </article>
    <article class="card feature" style="left:780px">
      <div class="fill" role="img" aria-label="Illustration of a person reviewing a checklist on a board" style="left:95px;top:17px;width:120px;height:113px;background:#f3ede9"></div>
      <h3 class="serif" style="font-weight:400">Reiciendis Voluptatib</h3>
      <p>Soiejpiciatis unde omnis iste natus error sit voluptatem accusantium doloremque laudantium, totam rem aperiam, eaque ipsa quae ab illo inventore veritatis et quasi</p>
      <div class="more"><u>Learn More</u><span class="arrow"><svg width="11" height="11" viewBox="0 0 11 11"><path d="M2 5.5h7M6 2.5l3 3-3 3" stroke="#fff" stroke-width="1.4" fill="none"/></svg></span></div>
    </article>
    <div class="abs dots-nav center" style="top:2264px"><span class="on"></span><span></span><span></span></div>
  </section>

  <!-- Blog -->
  <section>
    <div class="abs blog-band" role="img" aria-label="Soft grey background with flowing line texture"></div>
    <p class="abs kicker center" style="top:2446px">LATEST BLOG</p>
    <h2 class="abs serif h2 center" style="top:2477px">Our Blog</h2>
    <div class="abs rule" style="left:553px;top:2529px;width:94px"></div>

    <article class="card post" style="left:112px">
      <div class="fill" role="img" aria-label="Illustration of two colleagues in front of a large profile dashboard" style="left:120px;top:10px;width:226px;height:175px;background:linear-gradient(135deg,#e8ecf7,#f2f2f2)"></div>
      <p class="tag">Tenetur Asapiente</p>
      <h3 class="serif">Reiciendis voluptatibus maioresalias consequatur</h3>
      <p class="meta"><svg class="ico" width="13" height="13" viewBox="0 0 13 13"><circle cx="6.5" cy="6.5" r="5.5" fill="none" stroke="#f0520f"/><path d="M6.5 3.5v3h2" stroke="#f0520f" fill="none"/></svg>December 07, 2021<span class="gap"></span><svg class="ico" width="18" height="12" viewBox="0 0 18 12"><ellipse cx="9" cy="5.5" rx="8.5" ry="5" fill="#f0520f"/><path d="M4 9l-2 3 5-2z" fill="#f0520f"/></svg>14 Comments</p>
    </article>
    <article class="card post" style="left:623px">
      <div class="fill" role="img" aria-label="Illustration of a team meeting around a table with charts" style="left:80px;top:10px;width:306px;height:175px;background:linear-gradient(135deg,#eef1f3,#f5f1ea)"></div>
      <p class="tag">Tenetur Asapiente</p>
      <h3 class="serif">Reiciendis voluptatibus maioresalias consequatur</h3>
      <p class="meta"><svg class="ico" width="13" height="13" viewBox="0 0 13 13"><circle cx="6.5" cy="6.5" r="5.5" fill="none" stroke="#f0520f"/><path d="M6.5 3.5v3h2" stroke="#f0520f" fill="none"/></svg>December 07, 2021<span class="gap"></span><svg class="ico" width="18" height="12" viewBox="0 0 18 12"><ellipse cx="9" cy="5.5" rx="8.5" ry="5" fill="#f0520f"/><path d="M4 9l-2 3 5-2z" fill="#f0520f"/></svg>14 Comments</p>
    </article>
    <div class="abs pill" style="left:527px;top:2947px;width:145px;height:36px;line-height:36px">View More</div>
  </section>

  <!-- Subscribe -->
  <section>
    <p class="abs kicker" style="left:114px;top:3152px">SUBSCRIBE NOW</p>
    <h2 class="abs serif" style="left:114px;top:3180px;font-size:41px;line-height:54px">Get Latest Updates By<br>Subsribing Us</h2>
    <div class="abs mail" style="left:621px;top:3177px;width:465px"><span class="ph">Enter Mail</span><span class="btn" style="width:112px">Submit</span></div>
    <p class="abs member" style="left:635px;top:3232px">Already a member? <b>Sign In</b></p>
  </section>

  <!-- Footer -->
  <footer>
    <div class="abs" style="left:111px;top:3356px;width:978px;height:1px;background:var(--line)"></div>
    <div class="abs brand" style="left:111px;top:3448px;font-size:56px;line-height:1">velrato</div>

    <div class="abs f-col" style="left:424px;top:3402px"><h4 class="serif">Quick Links</h4><div class="u"></div><ul><li>Home</li><li>About Us</li><li>Our Features</li><li>FAQs</li><li>Contact Us</li></ul></div>
    <div class="abs f-col" style="left:621px;top:3402px"><h4 class="serif">Links</h4><div class="u"></div><ul><li>Team</li><li>About Us</li><li>Careers</li><li>Our Values</li></ul></div>
    <div class="abs f-col" style="left:783px;top:3402px"><h4 class="serif">Support</h4><div class="u"></div><ul><li>Copyright</li><li>Legal</li><li>Privacy</li><li>Accessibility</li><li>Sitemap</li></ul></div>
    <div class="abs f-col" style="left:957px;top:3402px"><h4 class="serif">Policies</h4><div class="u"></div><ul><li>Faq's</li><li>Terms &amp; Conditions</li><li>Privacy Policy</li><li>Site Map</li><li>Cookies Policy</li></ul></div>

    <div class="abs" style="left:1110px;top:3577px;width:44px;height:44px;border-radius:50%;background:var(--orange)"><svg width="44" height="44" viewBox="0 0 44 44"><path d="M18 24l4-4 4 4" stroke="#fff" stroke-width="1.6" fill="none"/></svg></div>
    <div class="abs" style="left:111px;top:3606px;width:978px;height:1px;background:var(--line)"></div>
    <p class="abs" style="left:111px;top:3630px;font-size:12.5px;color:#333">Copyright © 2022 | All Rights Reserved</p>
    <p class="abs legal" style="left:801px;top:3632px">TERMS &amp; CONDITIONS</p>
    <span class="abs" style="left:956px;top:3630px;color:var(--orange);font-size:12px">|</span>
    <p class="abs legal" style="left:981px;top:3632px">PRIVACY POLICY</p>
  </footer>

</div>
</body>
</html>
```